New Business Card Design Project

Use the flyer uploaded and website www.brightoakbuilders.com for inspiration.
List Our Services on Backside of business cards
Marcus Delling
Harborline Builders Inc.
Licensed General Contractors
858-471-6093

Contact Information for Business Card

Use the flyer uploaded and website www.brightoakbuilders.com for inspiration. List Our Services on Backside of business cards Marcus Delling Harborline Builders Inc. Licensed General Contractors 858-471-6093

```html
<!DOCTYPE html>
<html lang="en">
<head>
<meta charset="utf-8">
<title>Harborline Builders – Business Card</title>
<link href="https://fonts.googleapis.com/css2?family=Montserrat:wght@400;500;700&display=swap" rel="stylesheet">
<style>
  :root {
    --stage: #3b3b3b;
    --card: #1d1d1d;
    --ink: #f2f2f2;
    --ink-soft: #d6d6d6;
    --rule: #bdbdbd;
  }
  * { margin: 0; padding: 0; box-sizing: border-box; }
  html, body {
    width: 1200px; height: 1186px; overflow: hidden;
    background: var(--stage);
    font-family: "Montserrat", sans-serif;
    color: var(--ink);
  }
  .sheet {
    width: 1200px; height: 1186px;
    display: flex; flex-direction: column; align-items: center; justify-content: center;
    gap: 56px;
  }
  .card {
    width: 900px; height: 514px;
    background: var(--card);
    border-radius: 26px;
    position: relative;
    display: flex; flex-direction: column; align-items: center;
  }
  .brand {
    display: flex; align-items: center; gap: 14px;
    font-weight: 400; letter-spacing: 6px; text-transform: uppercase;
    color: var(--ink);
  }
  .brand-mark {
    width: 14px; height: 14px; border: 2px solid var(--ink); border-radius: 50%;
  }
  .card-back .brand { margin-top: 92px; font-size: 38px; }
  .services-title {
    margin-top: 44px;
    font-weight: 700; font-size: 24px;
    padding-bottom: 6px;
    border-bottom: 1.5px solid var(--rule);
  }
  .services {
    margin-top: 34px;
    list-style: none;
    display: flex; flex-wrap: wrap; justify-content: center;
    width: 800px; row-gap: 16px; column-gap: 30px;
    font-size: 17px; color: var(--ink-soft);
  }
  .services li::before { content: "•"; margin-right: 10px; color: var(--ink); }

  .card-front .brand { margin-top: 118px; font-size: 42px; }
  .contact-row {
    margin-top: 72px;
    display: flex; align-items: center; gap: 34px;
  }
  .person { text-align: right; }
  .person-name { font-weight: 700; font-size: 34px; line-height: 1.1; }
  .person-role { font-size: 19px; color: var(--ink-soft); margin-top: 2px; }
  .divider { width: 2px; height: 108px; background: var(--rule); }
  .contact-list { list-style: none; display: flex; flex-direction: column; gap: 12px; font-size: 19px; color: var(--ink-soft); }
  .contact-list li { display: flex; align-items: center; gap: 16px; }
  .contact-list svg { width: 18px; height: 18px; fill: var(--ink); flex: none; }
  .license { position: absolute; bottom: 58px; font-size: 19px; color: var(--ink-soft); letter-spacing: 0.5px; }
</style>
</head>
<body>
<main class="sheet">
  <section class="card card-back">
    <div class="brand"><span class="brand-mark"></span>Harborline Builders</div>
    <h2 class="services-title">Our Services</h2>
    <ul class="services">
      <li>Remodel: Kitchen &amp; Bath</li>
      <li>Painting: Interior &amp; Exterior</li>
      <li>Flooring: Carpet, Vinyl, Wood</li>
      <li>Window: Door Replacement</li>
      <li>Plumbing: Repair &amp; Upgrades</li>
      <li>Energy Efficient Upgrades</li>
      <li>Deck &amp; Patio construction</li>
      <li>Water &amp; Mold Damage</li>
      <li>Garage Renovation</li>
    </ul>
  </section>

  <section class="card card-front">
    <div class="brand"><span class="brand-mark"></span>Harborline Builders</div>
    <div class="contact-row">
      <div class="person">
        <div class="person-name">Marcus Delling</div>
        <div class="person-role">Managing Director</div>
      </div>
      <div class="divider"></div>
      <ul class="contact-list">
        <li>
          <svg viewBox="0 0 24 24" aria-hidden="true"><path d="M6.6 10.8a15.1 15.1 0 0 0 6.6 6.6l2.2-2.2a1 1 0 0 1 1-.25 11.4 11.4 0 0 0 3.6.57 1 1 0 0 1 1 1V20a1 1 0 0 1-1 1A17 17 0 0 1 3 4a1 1 0 0 1 1-1h3.5a1 1 0 0 1 1 1c0 1.25.2 2.45.57 3.57a1 1 0 0 1-.25 1z"/></svg>
          858-471-6093
        </li>
        <li>
          <svg viewBox="0 0 24 24" aria-hidden="true"><path d="M2 5h20v14H2z M2 5l10 8 10-8" fill="none" stroke="#f2f2f2" stroke-width="2"/></svg>
          info@brightoakbuilders.com
        </li>
        <li>
          <svg viewBox="0 0 24 24" aria-hidden="true"><circle cx="12" cy="12" r="9" fill="none" stroke="#f2f2f2" stroke-width="2"/><path d="M3 12h18M12 3c3 3 3 15 0 18M12 3c-3 3-3 15 0 18" fill="none" stroke="#f2f2f2" stroke-width="1.6"/></svg>
          www.brightoakbuilders.com
        </li>
      </ul>
    </div>
    <p class="license">CSLB Licensed No. #1048826</p>
  </section>
</main>
</body>
</html>
```